Cover für ein Ebook mit dem Thema Akne
Zielgruppe
Design für 80 % Junge Leute, sollte positives ausstrahlen und auch in Verbindung mit en bestimmten Farben wie Helltürkis oä. modern und profesionell wirken. Es handelt sich um das Thema Akne aber auch ein großer Teil Ernährung und um die Psyche geht es ebenfalls.
es sollte etwas herausstechen durch Farben aber auch sehr modern wirken.
Aufgabenstellung
Es sollte die Aufmerksamkeit wecken und ein positives Gefühl vermitteln und nicht nur mit Grau weiss Schwarz 'trostlos' wirken. Es sollte etwas herausstechen. Titel des Buches :
Klare Tage- Haut begreifen und meistern.
Es sollte neugierig machen und das Cover sollte 'Hoffnung, positives und fröhliches spiegeln
gerne auch mit Farben, 2 maximal 3 'Bunte Farben' Grau, Schwarz und Weiss zähle ich nicht zu diesen Bunten Farben. Das Cover und vorallem die Schrift sollten auch bei keiner Vergrößerung also bei kleiner Darstellung auf einnem E- Reader lesbar und erkennbar sein.
Es sollte aber auch für Schwarz- Weiss Reader die keine Farben anzeigen, attraktiv aussehen.
Auf dem Cover sollte der Name sein : Lukas Stein
Und der Titel : Klare Tage- Haut begreifen und meistern

```html
<!DOCTYPE html>
<html lang="de">
<head>
<meta charset="utf-8">
<title>Klare Tage – Ebook Cover</title>
<link rel="stylesheet" href="https://fonts.googleapis.com/css2?family=Bebas+Neue&display=swap">
<style>
  :root {
    --page: #ffffff;
    --sky: #c6e5f8;
    --sky-soft: #d6eefb;
    --band-blue: #0a9bd2;
    --band-cyan: #18b9e6;
    --title-blue: #0b8fc8;
    --accent-orange: #f39200;
    --white: #ffffff;
    --figure-yellow: #f7cf2e;
    --figure-skin: #f3dcc9;
  }
  html, body {
    margin: 0;
    padding: 0;
    width: 1200px;
    height: 1200px;
    overflow: hidden;
    background: var(--page);
  }
  .cover {
    position: absolute;
    left: 301px;
    top: 201px;
    width: 557px;
    height: 789px;
    overflow: hidden;
    background: linear-gradient(to bottom, var(--sky) 0%, var(--sky-soft) 50%, var(--sky) 52%, var(--band-cyan) 54%, var(--band-blue) 60%, var(--band-blue) 100%);
    box-shadow: 2px 3px 4px rgba(0,0,0,0.18);
    font-family: "Bebas Neue", "Oswald", sans-serif;
  }
  .cover__illustration {
    position: absolute;
    left: 4px;
    top: 24px;
    width: 550px;
    height: 440px;
    border-radius: 40% 40% 8px 8px;
    background: radial-gradient(ellipse at 50% 30%, var(--figure-skin) 0%, rgba(243,220,201,0.6) 30%, rgba(247,207,46,0.75) 60%, rgba(198,229,248,0) 85%);
  }
  .cover__burst {
    position: absolute;
    left: 22px;
    top: 445px;
    width: 70px;
    height: 110px;
  }
  .title-box {
    position: absolute;
    left: 70px;
    top: 508px;
    width: 520px;
    height: 126px;
    background: var(--white);
    transform: rotate(-3deg);
    transform-origin: left top;
  }
  .title-box__text {
    position: absolute;
    left: 22px;
    top: 14px;
    margin: 0;
    font-size: 106px;
    line-height: 1;
    color: var(--title-blue);
    font-weight: 400;
    letter-spacing: 1px;
    white-space: nowrap;
  }
  .title-box__mark {
    color: var(--accent-orange);
    display: inline-block;
    transform: rotate(4deg) scale(1.12, 1.22);
    margin-left: 4px;
  }
  .subtitle-band {
    position: absolute;
    left: 54px;
    top: 650px;
    width: 462px;
    height: 68px;
    background: var(--accent-orange);
    transform: rotate(-3deg);
    transform-origin: left top;
  }
  .subtitle-band__text {
    position: absolute;
    left: 26px;
    top: 17px;
    margin: 0;
    font-size: 36px;
    line-height: 1;
    color: var(--white);
    font-weight: 400;
    letter-spacing: 0.5px;
    white-space: nowrap;
  }
  .author-tag {
    position: absolute;
    left: 337px;
    top: 697px;
    width: 135px;
    height: 37px;
    background: var(--white);
    display: flex;
    align-items: center;
    justify-content: center;
    font-size: 22px;
    color: var(--title-blue);
    letter-spacing: 0.5px;
  }
</style>
</head>
<body>
  <main class="cover">
    <div class="cover__illustration" role="img" aria-label="Illustration: Comicfigur im gelben T-Shirt mit Hautunreinheiten, die ratlos die Hände hebt"></div>

    <svg class="cover__burst" viewBox="0 0 70 110" aria-hidden="true">
      <polygon points="26,8 36,4 60,58 54,62" fill="var(--white)"/>
      <polygon points="2,42 6,34 58,72 54,78" fill="var(--white)"/>
      <polygon points="10,100 8,92 48,84 50,90" fill="var(--white)"/>
    </svg>

    <div class="title-box">
      <h1 class="title-box__text">KLARE TAGE<span class="title-box__mark">!</span></h1>
    </div>

    <div class="subtitle-band">
      <h2 class="subtitle-band__text">HAUT BEGREIFEN UND MEISTERN</h2>
    </div>

    <div class="author-tag">LUKAS STEIN</div>
  </main>
</body>
</html>
```